Looking for a dynamic business card for a pizzeria.

A business card with our food, logo, and space for name, title, email, website, phone. The card should convey quality, unique, amazing. On the front, I envision food photo or photos with the owners names and contact information. On the back, more food with locations, website, facebook, twitter, instagram icons. It should look polished, not cartoonish, or plain.
Target Market(s)
upscale, local food buyers, 30-50 years in age.
Industry/Entity Type
Restaurant
Contact Information for Business Card
Business Name: Bru'nettix, LLC
Website: www.brunettix.com
Back:
2 locations: (can list on the back of card)
1. Harborside
4087 Corlan Avenue
Marlow Bay, WA 98301
360-481-5067
2. Crestview Hill
7315 Wendmere Road
Marlow Bay, WA 98307
360-293-8840
front:
EDITABLE space for
Business name
Person's Name
title
2nd title
Email address
cell-phone number
Requirements
Must have
- logo
- my food photo or photos (no watermarks showing)
- locations on back
- Person contact information on front
- full bleed

```html
<!DOCTYPE html>
<html lang="en">
<head>
<meta charset="utf-8">
<title>Bru'nettix, LLC – Business Cards</title>
<link href="https://fonts.googleapis.com/css2?family=Open+Sans:wght@400;600;700&display=swap" rel="stylesheet">
<style>
  :root {
    --backdrop: #ebe6df;
    --card-white: #ffffff;
    --brand-green: #1f5a32;
    --brand-green-deep: #0f3a1e;
    --brand-green-light: #3f7a4c;
    --brand-red: #c0232e;
    --ink: #2b2b2b;
    --rule: #2f5b3a;
  }
  * { margin: 0; padding: 0; box-sizing: border-box; }
  html, body {
    width: 1200px; height: 913px; overflow: hidden;
    background: var(--backdrop);
    font-family: "Open Sans", Arial, sans-serif;
  }
  .sheet {
    position: relative; width: 1200px; height: 913px;
    display: flex; align-items: center; justify-content: center; gap: 50px;
  }
  .card {
    position: relative; width: 525px; height: 300px;
    border-radius: 14px; overflow: hidden;
    box-shadow: 0 6px 18px rgba(0,0,0,0.18);
  }

  /* Front */
  .card-front { background: var(--card-white); }
  .front-rule {
    position: absolute; left: 0; right: 0; top: 150px;
    height: 1px; background: var(--rule);
  }
  .brand {
    position: absolute; left: 28px; top: 38px;
    display: flex; align-items: center; gap: 10px;
  }
  .brand-name {
    font-size: 36px; font-weight: 600; letter-spacing: 1px;
    color: var(--brand-green);
  }
  .brand-dot {
    width: 30px; height: 30px; border-radius: 50%;
    background: var(--brand-red);
  }
  .company-name {
    position: absolute; left: 28px; top: 94px;
    font-size: 21px; font-weight: 700; color: var(--brand-red);
  }
  .person {
    position: absolute; left: 0; top: 170px;
    display: flex; align-items: stretch;
  }
  .person-accent { display: flex; gap: 3px; padding-left: 22px; }
  .person-accent span { width: 6px; }
  .person-accent .green { background: var(--brand-green); }
  .person-accent .red { background: var(--brand-red); }
  .person-text { padding-left: 10px; }
  .person-name {
    font-size: 20px; font-weight: 700; color: var(--brand-green);
    line-height: 1.1;
  }
  .person-title {
    font-size: 14px; font-weight: 600; color: var(--brand-red);
  }
  .contacts {
    position: absolute; left: 60px; top: 228px;
    list-style: none; font-size: 13px; color: var(--ink); line-height: 1.45;
  }
  .contacts li { display: flex; align-items: center; gap: 7px; }
  .contacts svg { width: 11px; height: 11px; fill: var(--brand-red); flex: none; }

  /* Back */
  .card-back {
    background: linear-gradient(135deg, var(--brand-green-light) 0%, var(--brand-green) 45%, var(--brand-green-deep) 100%);
    color: #fff;
  }
  .back-brand {
    position: absolute; left: 36px; top: 52px;
    display: flex; align-items: center; gap: 12px;
  }
  .back-brand .brand-name { color: #fff; font-size: 40px; }
  .back-brand .brand-dot { background: #fff; width: 34px; height: 34px; }
  .back-company {
    position: absolute; left: 36px; top: 112px;
    font-size: 22px; font-weight: 700;
  }
  .back-rule {
    position: absolute; left: 0; right: 0; top: 170px;
    height: 1px; background: rgba(255,255,255,0.7);
  }
  .location {
    position: absolute; top: 196px;
    font-size: 13px; line-height: 1.45; font-style: normal;
  }
  .location-one { left: 36px; }
  .location-two { left: 290px; }
</style>
</head>
<body>
<main class="sheet">

  <section class="card card-front" aria-label="Business card front">
    <div class="front-rule"></div>
    <div class="brand">
      <span class="brand-name">Bru'nettix</span>
      <span class="brand-dot" aria-hidden="true"></span>
    </div>
    <div class="company-name">BRU'NETTIX, LLC</div>
    <div class="person">
      <div class="person-accent"><span class="green"></span><span class="red"></span></div>
      <div class="person-text">
        <div class="person-name">MARCO DELLAVI</div>
        <div class="person-title">Director, President</div>
      </div>
    </div>
    <ul class="contacts">
      <li>
        <svg viewBox="0 0 24 24"><path d="M6.6 10.8a15 15 0 0 0 6.6 6.6l2.2-2.2a1 1 0 0 1 1-.25 11.4 11.4 0 0 0 3.6.57 1 1 0 0 1 1 1V20a1 1 0 0 1-1 1A17 17 0 0 1 3 4a1 1 0 0 1 1-1h3.5a1 1 0 0 1 1 1c0 1.25.2 2.45.57 3.57a1 1 0 0 1-.25 1z"/></svg>
        360-512-7704
      </li>
      <li>
        <svg viewBox="0 0 24 24"><path d="M2 5h20v14H2z M4 7v.5l8 5 8-5V7l-8 5z" fill-rule="evenodd"/></svg>
        info@marcodellavi.com
      </li>
      <li>
        <svg viewBox="0 0 24 24"><circle cx="12" cy="12" r="10"/></svg>
        www.brunettix.com
      </li>
    </ul>
  </section>

  <section class="card card-back" aria-label="Business card back">
    <div class="back-brand">
      <span class="brand-name">Bru'nettix</span>
      <span class="brand-dot" aria-hidden="true"></span>
    </div>
    <div class="back-company">BRU'NETTIX, LLC</div>
    <div class="back-rule"></div>
    <address class="location location-one">
      360-481-5067<br>
      Harborside 4087 Corlan<br>
      Avenue Marlow Bay, WA 98301
    </address>
    <address class="location location-two">
      360-293-8840<br>
      Crestview Hill 7315 Wendmere<br>
      Road Marlow Bay, WA 98307
    </address>
  </section>

</main>
</body>
</html>
```